K742 PowerPoint Presentation

As you can see the design of this PowerPoint isn't cohesive. There are a lot of images and words that give it a very jumbled and busy appeal. We want to turn this into a sharp, cohesive and visually appealing presentation without taking away too much of the information. Feel free to use the images to create your own artwork for the PowerPoint.

Please don't hesitate to contact me with any questions.

```html
<!DOCTYPE html>
<html lang="en">
<head>
<meta charset="utf-8">
<title>Project Title Here</title>
<link rel="stylesheet" href="https://fonts.googleapis.com/css2?family=Fira+Sans:wght@400;700&family=Fira+Sans+Condensed:wght@400;600&display=swap">
<style>
  :root {
    --blue-bright: #1a8ef0;
    --blue-mid: #0a6fd8;
    --blue-deep: #0057c8;
    --footer-navy: #0a2f9a;
    --bullet-blue: #0b54c9;
    --text-dark: #1a1a1a;
    --brand-ink: #2a3e5c;
    --white: #ffffff;
  }
  * { margin: 0; padding: 0; box-sizing: border-box; }
  html, body { width: 1200px; height: 900px; overflow: hidden; background: var(--white); }
  .slide { position: relative; width: 1200px; height: 900px; background: var(--white); overflow: hidden; }

  .slide-header { position: absolute; left: 0; top: 0; width: 1200px; height: 120px; }
  .slide-header svg { position: absolute; inset: 0; }
  .slide-title {
    position: absolute; left: 32px; top: 26px;
    font-family: "Fira Sans", sans-serif; font-weight: 700;
    font-size: 46px; line-height: 1.2; color: var(--white); letter-spacing: 0.2px;
  }
  .brand {
    position: absolute; right: 24px; top: 48px;
    font-family: "Fira Sans Condensed", sans-serif; font-weight: 600;
    font-size: 30px; line-height: 1; color: var(--brand-ink);
  }

  .point-list { position: absolute; left: 44px; top: 186px; list-style: none; }
  .point {
    display: flex; align-items: center; height: 38px;
    font-family: "Fira Sans Condensed", sans-serif; font-weight: 400;
    font-size: 30px; color: var(--text-dark); white-space: nowrap;
  }
  .point + .point { margin-top: 37px; }
  .point:nth-child(5) { margin-top: 41px; }
  .point-icon { width: 27px; height: 27px; margin-right: 19px; flex: none; }

  .slide-footer {
    position: absolute; left: 0; bottom: 0; width: 1200px; height: 41px;
    background: var(--footer-navy);
    font-family: "Fira Sans", sans-serif; font-weight: 400;
    font-size: 16px; color: var(--white);
    display: flex; align-items: center; padding-left: 15px;
  }
</style>
</head>
<body>
<div class="slide">
  <header class="slide-header">
    <svg width="1200" height="120" viewBox="0 0 1200 120" aria-hidden="true">
      <defs>
        <linearGradient id="headerFill" x1="0" y1="0" x2="1" y2="0">
          <stop offset="0" stop-color="#0057c8"/>
          <stop offset="0.5" stop-color="#1a8ef0"/>
          <stop offset="1" stop-color="#0a6fd8"/>
        </linearGradient>
      </defs>
      <polygon points="0,0 1000,0 928,117 0,117" fill="url(#headerFill)"/>
      <line x1="0" y1="116" x2="1200" y2="116" stroke="#0a6fd8" stroke-width="2"/>
      <polyline points="928,116 998,10 1200,10" fill="none" stroke="#0a6fd8" stroke-width="2"/>
    </svg>
    <h1 class="slide-title">Project Title Here</h1>
    <div class="brand">Calder Group</div>
  </header>

  <ul class="point-list">
    <li class="point"><svg class="point-icon" viewBox="0 0 28 28" aria-hidden="true"><circle cx="14" cy="14" r="14" fill="#0b54c9"/><polyline points="11,8 17,14 11,20" fill="none" stroke="#ffffff" stroke-width="3.5" stroke-linecap="round" stroke-linejoin="round"/></svg>Lorem ipsum dolor sit ipsum Lorem ipsum dolor sit ipsum Lorem ipsum</li>
    <li class="point"><svg class="point-icon" viewBox="0 0 28 28" aria-hidden="true"><circle cx="14" cy="14" r="14" fill="#0b54c9"/><polyline points="11,8 17,14 11,20" fill="none" stroke="#ffffff" stroke-width="3.5" stroke-linecap="round" stroke-linejoin="round"/></svg>Lorem ipsum dolor sit ipsum Lorem ipsum dolor sit ipsum Lorem ipsum</li>
    <li class="point"><svg class="point-icon" viewBox="0 0 28 28" aria-hidden="true"><circle cx="14" cy="14" r="14" fill="#0b54c9"/><polyline points="11,8 17,14 11,20" fill="none" stroke="#ffffff" stroke-width="3.5" stroke-linecap="round" stroke-linejoin="round"/></svg>Lorem ipsum dolor sit ipsum Lorem ipsum dolor sit ipsum Lorem ipsum</li>
    <li class="point"><svg class="point-icon" viewBox="0 0 28 28" aria-hidden="true"><circle cx="14" cy="14" r="14" fill="#0b54c9"/><polyline points="11,8 17,14 11,20" fill="none" stroke="#ffffff" stroke-width="3.5" stroke-linecap="round" stroke-linejoin="round"/></svg>Lorem ipsum dolor sit ipsum Lorem ipsum dolor sit ipsum Lorem ipsum</li>
    <li class="point"><svg class="point-icon" viewBox="0 0 28 28" aria-hidden="true"><circle cx="14" cy="14" r="14" fill="#0b54c9"/><polyline points="11,8 17,14 11,20" fill="none" stroke="#ffffff" stroke-width="3.5" stroke-linecap="round" stroke-linejoin="round"/></svg>Lorem ipsum dolor sit ipsum Lorem ipsum dolor sit ipsum Lorem ipsum</li>
    <li class="point"><svg class="point-icon" viewBox="0 0 28 28" aria-hidden="true"><circle cx="14" cy="14" r="14" fill="#0b54c9"/><polyline points="11,8 17,14 11,20" fill="none" stroke="#ffffff" stroke-width="3.5" stroke-linecap="round" stroke-linejoin="round"/></svg>Lorem ipsum dolor sit ipsum Lorem ipsum dolor sit ipsum Lorem ipsum</li>
    <li class="point"><svg class="point-icon" viewBox="0 0 28 28" aria-hidden="true"><circle cx="14" cy="14" r="14" fill="#0b54c9"/><polyline points="11,8 17,14 11,20" fill="none" stroke="#ffffff" stroke-width="3.5" stroke-linecap="round" stroke-linejoin="round"/></svg>Lorem ipsum dolor sit ipsum Lorem ipsum dolor sit ipsum Lorem ipsum</li>
    <li class="point"><svg class="point-icon" viewBox="0 0 28 28" aria-hidden="true"><circle cx="14" cy="14" r="14" fill="#0b54c9"/><polyline points="11,8 17,14 11,20" fill="none" stroke="#ffffff" stroke-width="3.5" stroke-linecap="round" stroke-linejoin="round"/></svg>Lorem ipsum dolor sit ipsum Lorem ipsum dolor sit ipsum Lorem ipsum</li>
  </ul>

  <footer class="slide-footer">© 2014 K742, All Rights Reserved</footer>
</div>
</body>
</html>
```